Kelvaro.ch is looking for business card letterhead and envelope C5 with WOW effect

We need a strong business card for our company Kelvaro.ch, logo is available. You want a black or dark background on which the logo Stark r% 26 # 252; appears. Letterhead and envelope in C5 format should be in a similar design, but does not have to be We need a strong business card for our company Kelvaro.ch, logo is available. A black or dark background is desired, on which the logo Stark comes across. The letterhead and the envelope in C5 format should have a similar design.

Target Market(s)

Private customers as well as entrepreneurs

Contact Information for Business Card

E-mail: info@kelvaro-example.ch
Web.www.Kelvaro-example.ch
Tel: +41 ( 0 ) 79 482 6037
Adresse:
Lindenweg 14
9406 Tarnbach

Hier kann man Icons verwenden für Email,Tel und Adressse

Font styles to use
Other font styles liked:
• Dubai,bold

Colors

Designer to choose colors to be used in the design.

Requirements
Must have
• WOW effect
Nice to have
• R% 26 # 252; back business card with our service listings. - VEHICLE LABELING - SHOP WINDOW LABELING - STICKERS AND MUCH MORE ... in red color

```html
<!DOCTYPE html>
<html lang="en">
<head>
<meta charset="utf-8">
<title>Kelvaro.ch – Business Card</title>
<link href="https://fonts.googleapis.com/css2?family=Arimo:wght@400;700&display=swap" rel="stylesheet">
<style>
  :root{
    --backdrop:#2a2a2b;
    --card:#1d1d1e;
    --card-edge:#262627;
    --yellow:#f6c21c;
    --red:#e0161d;
    --text:#f1f1f1;
    --rule:#6a6a6a;
  }
  *{margin:0;padding:0;box-sizing:border-box}
  html,body{width:1200px;height:1108px;overflow:hidden;background:var(--backdrop)}
  body{font-family:"Arimo",Arial,sans-serif;color:var(--text);position:relative}
  .card{
    position:absolute;top:244px;width:400px;height:620px;
    background:var(--card);border-radius:22px;
    box-shadow:0 18px 40px rgba(0,0,0,.45);overflow:hidden;
  }
  .card--front{left:160px}
  .card--back{left:640px}

  /* front */
  .brand{
    position:absolute;top:150px;left:0;right:0;
    display:flex;align-items:center;justify-content:center;gap:16px;
  }
  .brand__square{width:26px;height:26px;background:var(--yellow)}
  .brand__name{font-weight:700;font-size:42px;color:var(--text);letter-spacing:.5px}
  .contact-icons{
    position:absolute;top:350px;left:40px;right:40px;
    display:flex;align-items:center;gap:10px;
  }
  .contact-icons__line{flex:1;height:1px;background:var(--rule)}
  .contact-icons__set{display:flex;gap:7px}
  .icon-tile{width:34px;height:34px;background:var(--yellow);border-radius:4px;display:flex;align-items:center;justify-content:center}
  .icon-tile svg{width:22px;height:22px}
  .contact-list{position:absolute;top:402px;left:0;right:0;text-align:center;font-size:22px;line-height:31px}
  .contact-list__web{color:var(--yellow)}
  .contact-divider{position:absolute;top:506px;left:40px;right:40px;height:1px;background:var(--rule)}
  .address{position:absolute;top:524px;left:0;right:0;text-align:center;font-size:22px;line-height:31px}

  /* back */
  .texture{
    position:absolute;inset:0 0 200px 0;
    background:linear-gradient(180deg,#2b2b2c 0%,#232324 60%,var(--card) 100%);
  }
  .back-brand{
    position:absolute;top:330px;left:0;right:0;text-align:center;
    font-weight:700;font-size:30px;color:var(--yellow);
  }
  .services{
    position:absolute;top:486px;left:0;right:0;text-align:center;
    list-style:none;color:var(--red);font-size:19px;line-height:28px;text-transform:uppercase;
  }
</style>
</head>
<body>

<section class="card card--front" aria-label="Business card front">
  <div class="brand">
    <span class="brand__square"></span>
    <span class="brand__name">Kelvaro.ch</span>
  </div>

  <div class="contact-icons">
    <span class="contact-icons__line"></span>
    <div class="contact-icons__set">
      <span class="icon-tile" aria-label="Phone">
        <svg viewBox="0 0 24 24"><path d="M6.6 10.8c1.4 2.8 3.8 5.2 6.6 6.6l2.2-2.2c.3-.3.7-.4 1-.2 1.1.4 2.3.6 3.6.6.6 0 1 .4 1 1V20c0 .6-.4 1-1 1C10.6 21 3 13.4 3 4c0-.6.4-1 1-1h3.5c.6 0 1 .4 1 1 0 1.3.2 2.5.6 3.6.1.3 0 .7-.2 1z" fill="#1d1d1e"/></svg>
      </span>
      <span class="icon-tile" aria-label="Email">
        <svg viewBox="0 0 24 24"><rect x="3" y="6" width="18" height="12" fill="none" stroke="#1d1d1e" stroke-width="2"/><path d="M3 6l9 7 9-7" fill="none" stroke="#1d1d1e" stroke-width="2"/></svg>
      </span>
      <span class="icon-tile" aria-label="Website">
        <svg viewBox="0 0 24 24"><circle cx="12" cy="12" r="8" fill="none" stroke="#1d1d1e" stroke-width="2"/><path d="M4 12h16M12 4c3 3 3 13 0 16M12 4c-3 3-3 13 0 16" fill="none" stroke="#1d1d1e" stroke-width="1.6"/></svg>
      </span>
    </div>
    <span class="contact-icons__line"></span>
  </div>

  <div class="contact-list">
    <div>+41 ( 0 ) 79 482 6037</div>
    <div>info@kelvaro-example.ch</div>
    <div class="contact-list__web">www.Kelvaro-example.ch</div>
  </div>
  <div class="contact-divider"></div>
  <div class="address">
    <div>Lindenweg 14</div>
    <div>9406 Tarnbach</div>
  </div>
</section>

<section class="card card--back" aria-label="Business card back">
  <div class="texture" role="img" aria-label="Faint dark tone-on-tone decorative pattern"></div>
  <div class="back-brand">Kelvaro.ch</div>
  <ul class="services">
    <li>Vehicle labeling</li>
    <li>Shop window labeling</li>
    <li>Stickers and much more ...</li>
  </ul>
</section>

</body>
</html>
```